Velvet Glow Co. Derma Roller packaging design

I need a box designed for a skin care brand called Velvet Glow Co. The box will be for our Derma Roller- a skin rejuvenation device. It will be sold online with lots of competition. I would like a modern, high end design, something that stands out and looks amazing. My logo is blush pink and black, for packaging i need no more than 3 colours, maybe gold if any other colour is used. A photo of a sample derma roller is attached below for an idea of what the product looks like, however my roller with have a clear handle with a black roller. The roller comes in a clear case, the box dimensions will need to be 16 cm long, 4 cm high, 4.5 cm wide.
ATTACHED ARE 2 SAMPLE BOXES AS AN EXAMPLE OF THE SIZE OF BOX REQUIRED!

Target Market(s)

25-50 year old women in the US

Colors
e667a6
000000
efefef

Requirements
Must have
• LOGO
• NAME OF PRODUCT- Cosmetic Derma Roller
• NEEDLE DEPTH- 0.25mm
• CAUTION- For personal use only, Do not use if allergic to metal, Do not use on open skin, wounds or active acne, sterilise roller before and after use.
Nice to have
• BENEFITS- Skin Rejuvenation, Collagen Induction Therapy, Increase product absorption, reduce acne scars and pigmentation
• FEATURES- 540 high quality titanium needles, ultra sharp needle tips, cross-line needle arrangement, ergonomic handle, anti slip grip,

```html
<!DOCTYPE html>
<html lang="en">
<head>
<meta charset="utf-8">
<title>Velvet Glow Co. – Cosmetic Derma Roller Packaging</title>
<link rel="stylesheet" href="https://fonts.googleapis.com/css2?family=Oswald:wght@400;500&display=swap">
<style>
  :root {
    --canvas-bg: #fbf7f5;
    --blush: #fdd5cf;
    --white: #ffffff;
    --ink: #111111;
    --rose-gold-light: #f0c9b6;
    --rose-gold: #d39a82;
    --rose-gold-deep: #b97a63;
  }
  * { box-sizing: border-box; margin: 0; padding: 0; }
  html, body { width: 1200px; height: 1200px; overflow: hidden; }
  body {
    background: var(--canvas-bg);
    position: relative;
    font-family: "Oswald", "Arial Narrow", sans-serif;
  }
  .panel {
    position: absolute;
    left: 48px;
    width: 1104px;
    height: 356px;
    overflow: hidden;
    background: repeating-linear-gradient(
      45deg,
      var(--blush) 0 51px,
      var(--white) 51px 102px
    );
  }
  .panel--front { top: 182px; }
  .panel--back  { top: 662px; }

  .front-label {
    position: absolute;
    left: 386px;
    top: 40px;
    width: 332px;
    height: 280px;
    background: var(--white);
    border: 3px solid transparent;
    border-image: linear-gradient(135deg, var(--rose-gold-light), var(--rose-gold-deep), var(--rose-gold-light), var(--rose-gold)) 1;
    display: flex;
    flex-direction: column;
    align-items: center;
  }
  .brand-name {
    margin-top: 96px;
    font-size: 30px;
    font-weight: 400;
    letter-spacing: 4px;
    color: var(--ink);
  }
  .product-title {
    font-weight: 500;
    font-size: 30px;
    letter-spacing: 0.5px;
    background: linear-gradient(90deg, var(--rose-gold-light), var(--rose-gold), var(--rose-gold-deep), var(--rose-gold-light), var(--rose-gold));
    -webkit-background-clip: text;
    background-clip: text;
    color: transparent;
    white-space: nowrap;
  }
  .front-label .product-title { margin-top: auto; margin-bottom: 28px; }

  .info-label {
    position: absolute;
    left: 248px;
    top: 58px;
    width: 608px;
    height: 238px;
    background: var(--white);
    padding: 24px 30px 0 29px;
  }
  .info-label .product-title { text-align: center; margin-bottom: 14px; }
  .spec {
    font-size: 13.6px;
    line-height: 18.4px;
    font-weight: 400;
    color: var(--ink);
    text-transform: uppercase;
    margin-bottom: 18px;
  }
</style>
</head>
<body>
  <section class="panel panel--front">
    <div class="front-label">
      <div class="brand-name">VELVET GLOW CO.</div>
      <h1 class="product-title">COSMETIC DERMA ROLLER</h1>
    </div>
  </section>

  <section class="panel panel--back">
    <div class="info-label">
      <h2 class="product-title">COSMETIC DERMA ROLLER</h2>
      <p class="spec">Benefits: skin rejuvenation, collagen induction therapy, increase product absorption, reduce acne scars and pigmentation</p>
      <p class="spec">Features: 540 high quality 0.25 mm titanium needles, ultra sharp needle tips, cross-line needle arrangement, ergonomic handle, anti slip grip</p>
      <p class="spec">Caution: for personal use only, do not use if allergic to metal, do not use on open skin, wounds or active acne, sterilise roller before and after use.</p>
    </div>
  </section>
</body>
</html>
```